U.S. Popcorn company needs business cards

We are a popcorn company that manufactures popcorn and sells it to grocery stores worldwide. Our theme is "Americana" and our logo is U.S. route 66 which is the most famous highway in the U.S.

We would like the design to be simple and to use both sides. On the back side we would like to see just the logo and website. The front would be normal details

Target Market(s)

Wholesalers, grocers and distributors

Industry/Entity Type

Manufacture

Contact Information for Business Card

Business name: Prairie Lantern Popcorn
Phone: +1 555 308 4726
Email: Dale@prairielanternpopcorn.com
website: www.prairielanternpopcorn.com
Tag Line: "POPular for a reason"
Name: Dale Whitcombe
Title: Founder/President

Requirements
Must have
• Either this design should be fun or clean and simple. I will let you show me your thougths.
Nice to have
• Anything that ties in the real Hwy Route 66.
• Colors might need to be red, white and blue incorporated.
Should not have
• Not be too busy.

```html
<!DOCTYPE html>
<html lang="en">
<head>
<meta charset="utf-8">
<title>Prairie Lantern Popcorn – Business Card</title>
<link href="https://fonts.googleapis.com/css2?family=Source+Sans+3:ital,wght@0,400;0,600;0,700;1,600&display=swap" rel="stylesheet">
<style>
  :root {
    --backdrop: #55473a;
    --card-white: #ffffff;
    --brand-red: #e31e24;
    --brand-navy: #0f2d6b;
    --ink-grey: #4a4a4a;
  }
  * { box-sizing: border-box; margin: 0; padding: 0; }
  html, body {
    width: 1200px; height: 987px; overflow: hidden;
    background: var(--backdrop);
    font-family: "Source Sans 3", "Myriad Pro", Arial, sans-serif;
  }
  .canvas { position: relative; width: 1200px; height: 987px; }
  .card {
    position: absolute; left: 293px; width: 615px; height: 352px;
  }
  .card--front { top: 130px; background: var(--card-white); }
  .card--back  { top: 506px; background: var(--brand-red); }

  .brand-name {
    position: absolute; text-align: center; font-weight: 700;
    text-transform: uppercase; line-height: 1.05; letter-spacing: 0.5px;
  }
  .card--front .brand-name {
    left: 28px; top: 95px; width: 310px; font-size: 38px; color: var(--brand-navy);
  }
  .card--back .brand-name {
    left: 158px; top: 110px; width: 300px; font-size: 34px; color: var(--card-white);
  }

  .person {
    position: absolute; right: 36px; top: 188px; text-align: right;
  }
  .person__name {
    font-size: 24px; font-weight: 600; color: var(--brand-navy);
    text-transform: uppercase; line-height: 1;
  }
  .person__title {
    margin-top: 6px; font-size: 17px; color: var(--brand-red); line-height: 1;
  }
  .accent-bar {
    position: absolute; right: 0; top: 191px; width: 9px; height: 49px;
    background: var(--brand-navy);
  }
  .contacts {
    position: absolute; right: 36px; top: 254px; list-style: none; text-align: right;
  }
  .contacts li {
    display: flex; justify-content: flex-end; align-items: center;
    gap: 10px; height: 23.5px; font-size: 15px; color: var(--ink-grey);
  }
  .contacts svg { width: 15px; height: 15px; fill: var(--brand-navy); }

  .tagline {
    position: absolute; left: 0; right: 0; top: 297px; text-align: center;
    font-size: 18px; font-weight: 600; color: var(--card-white);
  }
  .tagline em { font-style: italic; }
</style>
</head>
<body>
<main class="canvas">
  <section class="card card--front" aria-label="Business card front">
    <div class="brand-name">Prairie Lantern Popcorn</div>
    <div class="person">
      <div class="person__name">Dale Whitcombe</div>
      <div class="person__title">Founder/President</div>
    </div>
    <div class="accent-bar"></div>
    <ul class="contacts">
      <li>+1 555 308 4726
        <svg viewBox="0 0 24 24" aria-hidden="true"><path d="M6.6 10.8c1.4 2.8 3.8 5.1 6.6 6.6l2.2-2.2c.3-.3.7-.4 1-.2 1.1.4 2.3.6 3.6.6.6 0 1 .4 1 1V20c0 .6-.4 1-1 1C10.6 21 3 13.4 3 4c0-.6.4-1 1-1h3.5c.6 0 1 .4 1 1 0 1.3.2 2.5.6 3.6.1.3 0 .7-.2 1z"/></svg>
      </li>
      <li>Dale@prairielanternpopcorn.com
        <svg viewBox="0 0 24 24" aria-hidden="true"><path d="M2 5h20v14H2z M2 5l10 8 10-8" fill="none" stroke="#0f2d6b" stroke-width="0"/><path d="M2 5h20v2l-10 7L2 7z"/><path d="M2 9l10 7 10-7v10H2z"/></svg>
      </li>
      <li>www.prairielanternpopcorn.com
        <svg viewBox="0 0 24 24" aria-hidden="true"><circle cx="12" cy="12" r="10"/><path d="M7 8c2-1 3 1 5 0s1 3-1 4-3 3-1 5c-3 0-5-3-5-5s1-3 2-4zm8 4c2-1 4 0 4 2s-2 4-4 4c1-2-2-4 0-6z" fill="#ffffff"/></svg>
      </li>
    </ul>
  </section>

  <section class="card card--back" aria-label="Business card back">
    <div class="brand-name">Prairie Lantern Popcorn</div>
    <p class="tagline">POP<em>ular for a reason</em></p>
  </section>
</main>
</body>
</html>
```